GearHive.com

Our company, GearHive Inc., is an established business with an extensive worldwide customer base in the Aviation, Aerospace, and Defense Industries.
GearHive Inc, is an e-commerce platform driven by an aviation parts locator. We are looking to totally redo our homepage, log-in page, standard part search page, and results page.
Our current web design is in 800frame and we need it to be updated to a centered 1280 frame. The new design also needs to be easily viewed from any mobile device. The new size needs to accommodate 2-3 advertisements, both vertically and horizontally.
I like clean, simple, crisp lines that can easily be navigated by everyone. Along with Aviation/Aerospace stock photos, I would like to use different shades of blue and grey and accent specific buttons/drop-downs with orange or yellow.
We are also looking for a web designer who also has the ability to cut up the page and turn over to our .NET developers.
Attached are the 4 pages that I would like to start working on. The standard content within these pages need to be incorporated into the new design.
Our current website is www.gearhive.com
Below are some industry websites that I like the color and feel of.
Please use attached pic of corvane T410 as main photo
http://www.stravelcorp.com/
http://www.quillanor.com/en/aerospace.html
http://www.dexavend.com/
http://aerospace.veltrimax.com/

```html
<!DOCTYPE html>
<html lang="en">
<head>
<meta charset="utf-8">
<title>GearHive.com – Home</title>
<link href="https://fonts.googleapis.com/css2?family=Roboto:wght@400;500;700&display=swap" rel="stylesheet">
<style>
:root{
  --blue:#1f86dc;
  --blue-dark:#1470c4;
  --blue-light:#5fb2f0;
  --navy:#163f80;
  --purple:#52529a;
  --ink:#333;
  --grey-line:#c9c9c9;
  --orange:#f26b2a;
  --footer-dark:#232323;
  --white:#fff;
}
*{margin:0;padding:0;box-sizing:border-box}
html,body{width:946px;height:1200px;overflow:hidden;background:var(--white)}
body{position:relative;font-family:'Roboto',Arial,sans-serif;color:var(--ink)}
.abs{position:absolute}

/* header */
.header{left:0;top:0;width:946px;height:62px;background:var(--white)}
.header-band{right:0;top:0;width:571px;height:62px;background:var(--purple);clip-path:polygon(52px 0,100% 0,100% 100%,0 100%)}
.brand{left:140px;top:16px;font-size:30px;font-weight:700;color:var(--blue-dark);letter-spacing:-.5px}
.top-links{right:139px;top:27px;display:flex;gap:10px;font-size:10px;color:var(--white);letter-spacing:.2px}
.top-links span.sep{opacity:.8}

/* nav */
.nav{left:0;top:62px;width:946px;height:48px;background:linear-gradient(#2f94e4,#1a7fd6);box-shadow:0 2px 3px rgba(0,0,0,.2)}
.nav ul{list-style:none;display:flex;position:absolute;left:135px;top:0;height:48px}
.nav li{font-size:10.5px;color:var(--white);line-height:48px;padding:0 10px}
.nav li.active{background:var(--blue-light);padding:0 14px}

/* hero */
.hero{left:0;top:110px;width:946px;height:385px;background:linear-gradient(170deg,#c7d6e3 0%,#8fa9c4 35%,#4f6f93 70%,#5b6f80 100%)}
.hero-caption{left:412px;top:311px;width:396px;height:119px;background:rgba(55,55,55,.82);color:var(--white);padding:14px 13px}
.hero-caption h2{font-size:15.5px;font-weight:500;margin-bottom:6px}
.hero-caption p{font-size:11.5px;line-height:17px;padding-left:3px}
.btn{display:inline-block;background:linear-gradient(#2a93e6,#1676cf);color:var(--white);border-radius:2px;box-shadow:0 1px 2px rgba(0,0,0,.35);text-align:center}
.hero-caption .btn{margin:10px 0 0 3px;width:105px;height:25px;line-height:25px;font-size:11.5px}
.dots{left:717px;top:438px;display:flex;gap:8px}
.dots i{width:10px;height:10px;border-radius:50%;background:var(--white)}
.dots i.on{background:var(--blue)}

/* welcome */
.welcome-title,.service-title{font-size:16px;font-weight:500;color:var(--navy)}
.welcome-title{left:137px;top:532px}
.welcome-text{left:137px;top:562px;width:430px;font-size:12px;line-height:19.5px}
.read-more{left:472px;top:626px;width:91px;height:31px;line-height:31px;font-size:12.5px}
.service-title{left:611px;top:531px}
.service-list{left:611px;top:563px;width:198px;list-style:none}
.service-list li{display:flex;align-items:center;gap:20px;height:26px;font-size:12px;border-bottom:1px solid var(--grey-line)}
.service-list li:last-child{border-bottom:none}

/* feature band */
.features{left:0;top:681px;width:946px;height:230px;background:linear-gradient(#dfe6ee,#f2f5f8 60%,#e4eaf0)}
.card{top:721px;width:159px;height:156px;background:var(--white);border-bottom:3px solid var(--blue)}
.card .photo{height:100px}
.card p{font-size:11px;line-height:15px;text-align:center;padding-top:12px;color:#444}

/* testimonial */
.testimonial{left:0;top:911px;width:946px;height:149px;background:linear-gradient(#fafafa,#e8ebee)}
.quote-mark{font-size:28px;font-weight:700;color:#111;font-family:Georgia,serif}
.quote{left:156px;top:944px;font-size:13.5px;color:var(--purple)}
.author{left:0;top:970px;width:946px;text-align:center;font-size:11px;color:#555}
.more-testimonials{left:384px;top:1007px;width:175px;height:31px;line-height:31px;font-size:12.5px}

/* footer */
.footer{left:0;top:1060px;width:946px;height:89px;background:var(--purple);color:var(--white)}
.address{left:152px;top:1090px;font-size:10px;line-height:15px;color:var(--white)}
.pin{left:130px;top:1091px}
.social{left:401px;top:1092px;display:flex;gap:8px}
.social i{width:32px;height:32px;border-radius:2px}
.contact{right:146px;top:1090px;font-size:10px;line-height:15px;text-align:right;color:var(--white)}
.copyright{left:0;top:1149px;width:946px;height:51px;background:var(--footer-dark);color:var(--white);font-size:10px;text-align:center;line-height:51px}
</style>
</head>
<body>

<header class="abs header"></header>
<div class="abs header-band"></div>
<div class="abs brand">GearHive</div>
<nav class="abs top-links">
  <span>GEARHIVE MAIN</span><span class="sep">|</span>
  <span>SKYLEDGER</span><span class="sep">|</span>
  <span>MESSAGEBOARD</span><span class="sep">|</span>
  <span>LOG IN</span>
</nav>

<nav class="abs nav">
  <ul>
    <li class="active">HOME</li><li>ABOUT</li><li>MEBERSHIP</li><li>BUYERS</li><li>SUPPLIERS</li>
    <li>GOVERNMENT DATE</li><li>ADVERTISE</li><li>MEDIA</li><li>FAQ'S</li><li>CONTACT</li>
  </ul>
</nav>

<section class="abs hero" role="img" aria-label="Photo of a white business jet flying over a city and river"></section>
<div class="abs hero-caption">
  <h2>Government bidding? Detailed Longistics &amp; Notification</h2>
  <p>Updated Solicitation Information. Receive e-mail notification when a Government Solicotation Matches Your Inventory!</p>
  <span class="btn">LEARN MORE</span>
</div>
<div class="abs dots"><i></i><i class="on"></i><i></i><i></i><i></i></div>

<h2 class="abs welcome-title">WELCOME TO GEARHIVE</h2>
<p class="abs welcome-text">Lorem Ipsum is simply dummy text of the printing and typesetting industry. Lorem Ipsum has been the industry's standard dummy text ever since the 1500s, when an unknown printer took a galley of type and scrambled it to make a type specimen ting, remaining essentially unchanged.</p>
<span class="abs btn read-more">Read More</span>

<h2 class="abs service-title">OUR SERVICE</h2>
<ul class="abs service-list">
  <li><svg width="10" height="10" viewBox="0 0 10 10"><circle cx="5" cy="5" r="5" fill="#f26b2a"/><path d="M2.6 5.1l1.7 1.6 3.1-3.2" stroke="#fff" stroke-width="1.4" fill="none"/></svg>Solution</li>
  <li><svg width="10" height="10" viewBox="0 0 10 10"><circle cx="5" cy="5" r="5" fill="#f26b2a"/><path d="M2.6 5.1l1.7 1.6 3.1-3.2" stroke="#fff" stroke-width="1.4" fill="none"/></svg>Our Community</li>
  <li><svg width="10" height="10" viewBox="0 0 10 10"><circle cx="5" cy="5" r="5" fill="#f26b2a"/><path d="M2.6 5.1l1.7 1.6 3.1-3.2" stroke="#fff" stroke-width="1.4" fill="none"/></svg>Industry Connections</li>
  <li><svg width="10" height="10" viewBox="0 0 10 10"><circle cx="5" cy="5" r="5" fill="#f26b2a"/><path d="M2.6 5.1l1.7 1.6 3.1-3.2" stroke="#fff" stroke-width="1.4" fill="none"/></svg>Member Advantages</li>
</ul>

<section class="abs features" role="img" aria-label="Soft sky with clouds background"></section>
<article class="abs card" style="left:134px">
  <div class="photo" role="img" aria-label="Photo of a fighter jet on a carrier deck" style="background:linear-gradient(#8d8f8c,#c8b59a 60%,#6e6e6a)"></div>
  <p>Aviation, Aerospace, Military and Defense Locator service</p>
</article>
<article class="abs card" style="left:306px">
  <div class="photo" role="img" aria-label="Photo of a white helicopter in blue sky" style="background:linear-gradient(#3e8ed8,#8cc1ec)"></div>
  <p>Visit the GearHive Community Message Board</p>
</article>
<article class="abs card" style="left:478px">
  <div class="photo" role="img" aria-label="Photo of an airliner above sunlit clouds" style="background:linear-gradient(#8fa3c0,#dfe7f0 55%,#9aaac0)"></div>
  <p>Search Government Solicitation Win Contracts and Birds</p>
</article>
<article class="abs card" style="left:650px">
  <div class="photo" role="img" aria-label="Photo of a plane silhouette against a sunset sky" style="background:linear-gradient(135deg,#c98a52,#f4d9a0 55%,#e8b77a)"></div>
  <p>GearHive Marketing Reache your target Audience</p>
</article>

<section class="abs testimonial"></section>
<span class="abs quote-mark" style="left:135px;top:932px">“</span>
<p class="abs quote">We had an AOG Issue last night. i Logged in to gearHive.com and had the part orderd in about five minutes</p>
<span class="abs quote-mark" style="left:792px;top:928px">”</span>
<p class="abs author">-dara Velloc, Tallow Ridge Industries, Inc.</p>
<span class="abs btn more-testimonials">Read More testimonials</span>

<footer class="abs footer"></footer>
<svg class="abs pin" width="14" height="20" viewBox="0 0 14 20"><path d="M7 0C3.1 0 0 3.1 0 7c0 5 7 13 7 13s7-8 7-13c0-3.9-3.1-7-7-7zm0 10a3 3 0 110-6 3 3 0 010 6z" fill="#fff"/></svg>
<p class="abs address">GearHive, Inc. 418 Harbin Crest Road<br>Lindmoor, FL 30412</p>
<div class="abs social">
  <i style="background:#2ab0e6"></i><i style="background:#d8262a"></i><i style="background:#2d4f91"></i><i style="background:#1a6ab3"></i>
</div>
<p class="abs contact">Phone: 555.014.2270<br>Email:&nbsp; sales@gearhive.com</p>
<div class="abs copyright">Copyright © 2014 All Rights Reserved</div>

</body>
</html>
```